Dental Practice Website design

Design a new website for Brambleford Dental Practice.
Design should be warm, neutral in colour, with some small amount of bright colour if needed but kept to a minimum. Website should look professional, high end. Home page should be easy to navigate and simple for patients to be able to book online.
Logo in files along with some examples of websites that we like. Please ask if any further info needed.
Menu should have:
About
New Patients
Treatments
Fees
Contact Us

Industry/Entity Type

Dentistry

Number of Pages Required

4 page

Font styles to use
Sans Serif

Colors

Designer to choose colors to be used in the design.

Requirements
Must have
• Ravelle ratings badge, book online button,
Nice to have
• neutral, relaxing colours
Should not have
• harsh, bright colours!

```html
<!DOCTYPE html>
<html lang="en">
<head>
<meta charset="utf-8">
<title>Brambleford Dental Practice</title>
<link href="https://fonts.googleapis.com/css2?family=Lato:wght@300;400;700;900&display=swap" rel="stylesheet">
<style>
:root{
  --ink:#1b2a2e;
  --gold:#8a7650;
  --gold-light:#a38d62;
  --paper:#ffffff;
  --sand:#f1efeb;
  --card:#e9e8e5;
  --text:#4a4a4a;
  --muted:#5d5d5d;
  --light:#ffffff;
}
*{box-sizing:border-box;margin:0;padding:0}
html,body{width:1200px;height:4179px;overflow:hidden}
body{font-family:'Lato',sans-serif;color:var(--text);background:var(--paper);position:relative}
.abs{position:absolute}
a{color:inherit;text-decoration:none}
.btn{position:absolute;display:flex;align-items:center;justify-content:center;font-size:15px;color:#fff;background:var(--gold)}
.btn.dark{background:var(--ink)}
.accent{color:var(--gold)}
h2.section-title{position:absolute;left:0;width:1200px;text-align:center;font-size:40px;font-weight:700;color:var(--ink)}
.rule{position:absolute;height:3px;background:var(--gold);width:80px}

/* top bar & nav */
.topbar{left:0;top:0;width:1200px;height:42px;background:var(--ink);color:#fff;font-size:13px}
.topbar span{position:absolute;top:12px;display:flex;gap:8px;align-items:center}
.nav{left:0;top:42px;width:1200px;height:81px;background:#fff}
.nav ul{list-style:none;position:absolute;left:526px;top:26px;display:flex;gap:38px;font-size:15px;color:#333}
.nav li.active{background:var(--ink);color:#fff;font-weight:700;padding:3px 10px;margin:-3px -10px 0}
.brand{left:112px;top:42px;height:81px;display:flex;align-items:center;gap:12px;font-size:22px;font-weight:700;color:var(--ink)}
.brand i{display:block;width:14px;height:14px;background:var(--gold)}

/* hero */
.hero{left:0;top:123px;width:1200px;height:600px;background:linear-gradient(100deg,#5a5856 0%,#8a8785 40%,#b9b1a8 70%,#cfc4b8 100%)}
.hero h1{position:absolute;left:110px;top:115px;font-size:58px;line-height:64px;font-weight:900;color:#fff;width:520px}
.hero p{position:absolute;left:112px;top:323px;font-size:21px;line-height:31px;color:#fff;width:350px}
.arrow{position:absolute;top:273px;width:38px;height:38px;background:var(--ink);display:flex;align-items:center;justify-content:center}

/* about */
.photo{position:absolute}
.about-text{left:637px;top:905px;width:450px;font-size:14px;line-height:24px;color:var(--muted)}
.about-text p{margin-bottom:24px}

/* treatments */
.t-card{position:absolute;top:1429px;width:303px;text-align:center}
.t-card .img{height:241px}
.t-card h3{margin-top:16px;font-size:23px;color:var(--ink);font-weight:700}
.t-card p{margin:12px auto 0;width:270px;font-size:14px;line-height:23px;color:var(--muted)}
.t-card .btn{position:relative;margin:20px auto 0;width:146px;height:37px}

/* team */
.team{left:0;top:1939px;width:1200px;height:555px;background:var(--ink)}
.team-box{left:110px;top:2014px;width:633px;height:407px;background:rgba(138,118,80,.96);color:#fff}
.team-box h2{position:absolute;left:65px;top:40px;font-size:38px;font-weight:700}
.team-box .rule{left:65px;top:96px;background:#fff;width:60px;height:2px}
.team-box p{position:absolute;left:65px;top:122px;width:505px;font-size:14px;line-height:24px}

/* join */
.join{left:0;top:2494px;width:1200px;height:530px;background:var(--sand)}
.join-text{left:225px;top:2654px;width:750px;text-align:center;font-size:14.5px;line-height:26px;color:var(--muted)}
.join-text p{margin-bottom:12px}

/* why */
.why-sub{left:290px;top:3187px;width:620px;text-align:center;font-size:14.5px;line-height:23px;color:var(--muted)}
.w-card{position:absolute;top:3253px;width:227px;height:216px;background:var(--card);text-align:center;padding-top:18px}
.w-card h3{margin-top:8px;font-size:17px;line-height:23px;color:var(--ink);font-weight:700;padding:0 14px}
.w-card p{margin:8px auto 0;width:200px;font-size:14px;line-height:21px;color:var(--muted)}
.w-card.featured{background:var(--ink)}
.w-card.featured h3{color:var(--gold-light)}
.w-card.featured p{color:#fff}

/* testimonial & footer */
footer{color:var(--light)}
.footer{left:0;top:3652px;width:1200px;height:527px;background:var(--ink)}
.quote{left:112px;top:3556px;width:976px;height:234px;background:var(--gold);color:#fff}
.quote .mark{position:absolute;left:34px;top:22px;font-size:60px;font-weight:900;line-height:1}
.quote p{position:absolute;left:72px;top:46px;width:510px;font-size:16px;line-height:28px}
.quote .who{position:absolute;left:70px;top:168px;font-size:21px;font-weight:700}
.dots{position:absolute;left:438px;top:188px;display:flex;gap:9px}
.dots i{display:block;width:20px;height:5px;background:#fff}
.badge{left:926px;top:3743px;width:141px;height:68px;background:#fff;border-radius:6px}
.f-col{position:absolute;top:3860px;color:var(--light)}
.f-col h4{font-size:21px;font-weight:700;margin-bottom:28px}
.f-col ul{list-style:none;font-size:14.5px;line-height:38px}
.f-col p{font-size:14.5px;line-height:26px}
.contact-row{position:absolute;display:flex;gap:20px;font-size:14.5px;line-height:24px;color:var(--light)}
.socials{left:112px;top:4040px;display:flex;gap:10px;color:var(--light)}
.socials span{display:flex;align-items:center;height:34px;padding:0 8px;font-size:12px;border:1px solid rgba(255,255,255,.5)}
.socials span:first-child{background:var(--gold);border-color:var(--gold)}
.copyline{left:112px;top:4129px;width:976px;height:1px;background:rgba(255,255,255,.25)}
.copy{left:0;top:4146px;width:1200px;text-align:center;font-size:12.5px;color:var(--light)}
</style>
</head>
<body>

<header>
  <div class="abs topbar">
    <span style="left:608px">
      <svg width="14" height="14" viewBox="0 0 24 24" fill="#fff"><path d="M6.6 10.8a15 15 0 0 0 6.6 6.6l2.2-2.2a1 1 0 0 1 1-.25 11 11 0 0 0 3.6.6 1 1 0 0 1 1 1V20a1 1 0 0 1-1 1A17 17 0 0 1 3 4a1 1 0 0 1 1-1h3.5a1 1 0 0 1 1 1c0 1.25.2 2.45.6 3.6a1 1 0 0 1-.25 1z"/></svg>
      Call Us : +1 555 014 2290</span>
    <span style="left:818px">
      <svg width="15" height="12" viewBox="0 0 24 18"><path d="M1 1h22v16H1z" fill="#fff"/><path d="M1 1l11 8 11-8" stroke="#1b2a2e" stroke-width="2" fill="none"/></svg>
      Email : info@bramblefordental.com</span>
  </div>
  <nav class="abs nav">
    <ul>
      <li class="active">Home</li><li>About</li><li>New Patients</li><li>Treatments</li><li>Fees</li><li>Contact Us</li>
    </ul>
  </nav>
  <div class="abs brand"><i></i>Brambleford Dental Practice</div>
</header>

<section class="abs hero" role="img" aria-label="Photo of a smiling patient having a dental check-up with a mirror">
  <h1>CARING FOR YOUR SMILE, ONE VISIT AT A TIME</h1>
  <p>Experience exceptional dentistry in a calm and welcoming space.</p>
  <a class="btn dark" style="left:112px;top:419px;width:146px;height:37px">Book Online</a>
  <span class="arrow" style="left:36px"><svg width="12" height="12" viewBox="0 0 12 12"><path d="M8 1L3 6l5 5" stroke="#fff" stroke-width="1.6" fill="none"/></svg></span>
  <span class="arrow" style="left:1126px"><svg width="12" height="12" viewBox="0 0 12 12"><path d="M4 1l5 5-5 5" stroke="#fff" stroke-width="1.6" fill="none"/></svg></span>
</section>

<section>
  <div class="photo" style="left:112px;top:809px;width:454px;height:459px;background:linear-gradient(135deg,#cfd4d8,#9aa3aa 60%,#c2b3a4)" role="img" aria-label="Photo of a patient checking her smile in a hand mirror"></div>
  <h2 class="abs" style="left:637px;top:812px;font-size:40px;color:var(--ink)">About <span class="accent">Us</span></h2>
  <div class="rule" style="left:637px;top:862px"></div>
  <div class="abs about-text">
    <p>Welcome to our friendly dental practice nestled in the heart of beautiful Ashcombe, UK. Our team of dedicated dentists, hygienists and support staff are here to provide you with exceptional dental care. With a wide array of services, including general and cosmetic dentistry, orthodontics and emergency care, we're confident that we can deliver the highest quality treatment to you and your loved ones.</p>
    <p>At our practice, we believe that a visit to the dentist should be a comfortable and positive experience. We strive to create a warm and welcoming atmosphere where our patients can feel at ease and confident in the care they receive.</p>
  </div>
  <a class="btn" style="left:637px;top:1217px;width:146px;height:37px">Read More</a>
</section>

<section>
  <h2 class="section-title" style="top:1343px">Our <span class="accent">Treatments</span></h2>
  <div class="rule" style="left:540px;top:1393px;width:196px"></div>
  <article class="t-card" style="left:112px">
    <div class="img" style="background:linear-gradient(135deg,#dfe3e6,#8f969c)" role="img" aria-label="Photo of a smiling patient during a cosmetic treatment"></div>
    <h3>Cosmetic Dentistry</h3>
    <p>Excepteur sint occaecat cupidatat non proident, sunt in culpa qui officia deser mollit anim id est laborum.</p>
    <a class="btn">Read More</a>
  </article>
  <article class="t-card" style="left:449px">
    <div class="img" style="background:linear-gradient(135deg,#d9b8a6,#b07f6d)" role="img" aria-label="Photo of a clear orthodontic aligner being fitted"></div>
    <h3>Orthodontics</h3>
    <p>Excepteur sint occaecat cupidatat non proident, sunt in culpa qui officia deser mollit anim id est laborum.</p>
    <a class="btn">Read More</a>
  </article>
  <article class="t-card" style="left:785px">
    <div class="img" style="background:linear-gradient(135deg,#c7d6e4,#5d89b3)" role="img" aria-label="Photo of dental staff with a patient in the surgery"></div>
    <h3>Emergency Care</h3>
    <p>Excepteur sint occaecat cupidatat non proident, sunt in culpa qui officia deser mollit anim id est laborum.</p>
    <a class="btn">Read More</a>
  </article>
</section>

<section>
  <div class="abs team"></div>
  <div class="photo" style="left:600px;top:1939px;width:600px;height:555px;background:linear-gradient(120deg,#9fc0df,#3f74b5 55%,#2e5f9c)" role="img" aria-label="Photo of the dental team in blue scrubs"></div>
  <div class="abs team-box">
    <h2>Our Team</h2>
    <div class="rule"></div>
    <p>We are delighted to introduce you to our experienced and compassionate dental team. Our team comprises highly skilled dental professionals who are dedicated to providing you with high-quality dental care services. Led by our experienced dentist, each member of our team brings their own unique set of skills and expertise. From our friendly reception staff to our knowledgeable hygienists and assistants, our team is here to ensure that you receive personalised dental care that meets your unique needs and preferences.</p>
    <a class="btn dark" style="left:65px;top:320px;width:146px;height:37px">Read More</a>
  </div>
</section>

<section>
  <div class="abs join"></div>
  <h2 class="section-title" style="top:2568px">Join Our <span class="accent">Practice</span></h2>
  <div class="rule" style="left:560px;top:2618px;width:182px"></div>
  <div class="abs join-text">
    <p>If you're looking for an exceptional dental practice, we're here to help! Our team is made up of highly skilled professionals who are dedicated to ensuring that all our patients receive top-notch care in a welcoming and comfortable environment. Whether you need a routine examination or a more specialised treatment, we have all the resources to provide you with the best dental care possible. Our practice is always up-to-date with the latest techniques and technologies to make sure that our patients receive the best possible results.</p>
    <p>We understand that dental care can be expensive which is why we offer affordable prices to ensure that everyone has access to quality care. If you'd like to learn more about our practice, please don't hesitate to contact us.</p>
  </div>
  <a class="btn" style="left:460px;top:2900px;width:281px;height:37px">Book Your Appointment online!</a>
</section>

<section>
  <h2 class="section-title" style="top:3100px">Why <span class="accent">Choose Us?</span></h2>
  <div class="rule" style="left:548px;top:3150px;width:196px"></div>
  <p class="abs why-sub">At Brambleford Dental Practice, we believe in providing exceptional dental care in a warm and welcoming environment. Here's why patients trust us with their smiles:</p>
  <article class="w-card" style="left:112px">
    <svg width="60" height="56" viewBox="0 0 60 56" fill="none" stroke="#8a7650" stroke-width="1.6"><path d="M18 8c-8 0-12 7-10 16 2 8 4 24 9 24 4 0 4-12 9-12s5 12 9 12 7-16 9-24c2-9-2-16-10-16-4 0-6 2-8 2s-4-2-8-2z"/><path d="M40 26l8 3v7c0 5-4 8-8 9-4-1-8-4-8-9v-7z"/></svg>
    <h3>Comprehensive Dental Services</h3>
    <p>Excepteur sint occaecat cupidatat non proident, sunt culpa qui officia aborum.</p>
  </article>
  <article class="w-card" style="left:362px">
    <svg width="70" height="56" viewBox="0 0 70 56" fill="none" stroke="#8a7650" stroke-width="1.6"><circle cx="35" cy="16" r="7"/><circle cx="16" cy="22" r="6"/><circle cx="54" cy="22" r="6"/><path d="M22 48c0-10 6-16 13-16s13 6 13 16M6 48c0-8 4-13 10-13M64 48c0-8-4-13-10-13"/></svg>
    <h3>Experienced &amp; Friendly Team</h3>
    <p>Excepteur sint occaecat cupidatat non proident, sunt culpa qui officia aborum.</p>
  </article>
  <article class="w-card featured" style="left:611px">
    <svg width="64" height="56" viewBox="0 0 64 56" fill="none" stroke="#a38d62" stroke-width="1.6"><circle cx="38" cy="14" r="10"/><path d="M38 8v12M35 11h5M6 40l12-8c4-2 8-2 12 0l8 2c3 1 3 5 0 5H28M38 38l12-6c3-1 5 2 3 4L38 48H14L6 52"/></svg>
    <h3>Affordable &amp; Transparent Pricing</h3>
    <p>Excepteur sint occaecat cupidatat non proident, sunt culpa qui officia aborum.</p>
  </article>
  <article class="w-card" style="left:861px">
    <svg width="64" height="56" viewBox="0 0 64 56" fill="none" stroke="#8a7650" stroke-width="1.6"><circle cx="24" cy="24" r="10"/><circle cx="24" cy="24" r="4"/><path d="M24 10v-4M24 42v-4M10 24H6M42 24h-4"/><rect x="38" y="28" width="16" height="20" rx="3"/><path d="M42 34h8M42 40h8"/></svg>
    <h3>State-of-the-Art Technology</h3>
    <p>Excepteur sint occaecat cupidatat non proident, sunt culpa qui officia aborum.</p>
  </article>
</section>

<footer>
  <div class="abs footer"></div>
  <div class="abs quote">
    <span class="mark">&ldquo;</span>
    <p>Lorem ipsum dolor sit amet, consectetur adipiscing elit, sed do eiusmod tempor incididunt ut labore et dolore magna aliqua. Ut enim ad minim veniam, quis nostrud exercitation ullamco laboris nisi ut aliquip ex ea commodo consequat.</p>
    <span class="who">M. Hartley</span>
    <div class="dots"><i></i><i></i><i></i></div>
    <div class="photo" style="left:699px;top:0;width:277px;height:234px;background:linear-gradient(120deg,#8a7650,#b9b4ae 40%,#dcdad7)" role="img" aria-label="Portrait photo of a smiling patient"></div>
  </div>
  <div class="abs badge" role="img" aria-label="Ravelle ratings badge"></div>

  <div class="f-col" style="left:114px;width:260px">
    <h4>About Us</h4>
    <p>Our team of dedicated dentists, hygienists and support staff are here to provide you with exceptional dental care.</p>
  </div>
  <div class="abs socials">
    <span>Chatterly</span><span>Pictora</span><span>Linkwell</span><span>Vidstream</span>
  </div>

  <div class="f-col" style="left:436px"><h4>Contact Us</h4></div>
  <div class="contact-row" style="left:436px;top:3906px">
    <svg width="18" height="22" viewBox="0 0 18 22" fill="none" stroke="#fff" stroke-width="1.4"><path d="M9 21s7-7 7-12A7 7 0 0 0 2 9c0 5 7 12 7 12z"/><circle cx="9" cy="9" r="2.5"/></svg>
    <span>12 Brambleford Lane,<br>Ashcombe AB1 2CD</span>
  </div>
  <div class="contact-row" style="left:436px;top:3989px">
    <svg width="18" height="18" viewBox="0 0 24 24" fill="none" stroke="#fff" stroke-width="1.6"><path d="M6.6 10.8a15 15 0 0 0 6.6 6.6l2.2-2.2 4.6 1.3V20a1 1 0 0 1-1 1A17 17 0 0 1 3 4a1 1 0 0 1 1-1h3.5l1.2 4.6z"/></svg>
    <span>+1 555 014 2290</span>
  </div>
  <div class="contact-row" style="left:436px;top:4049px">
    <svg width="18" height="14" viewBox="0 0 24 18" fill="none" stroke="#fff" stroke-width="1.6"><rect x="1" y="1" width="22" height="16"/><path d="M1 1l11 8 11-8"/></svg>
    <span>info@bramblefordental.com</span>
  </div>

  <div class="f-col" style="left:778px">
    <h4>Quick Links</h4>
    <ul style="margin-top:-8px"><li>Home</li><li>About</li><li>New Patients</li><li>Treatments</li><li>Fees</li></ul>
  </div>
  <div class="f-col" style="left:979px">
    <h4>Other Links</h4>
    <ul style="margin-top:-8px"><li>Contact Us</li><li>Team</li><li>Practice</li><li>Blog</li><li>Security</li></ul>
  </div>
  <div class="abs copyline"></div>
  <p class="abs copy">Copyright © 2025 Brambleford Dental Practice. All Rights Reserved</p>
</footer>

</body>
</html>
```